Kestrel Facilities Business Card Design

We would now like to design business cards with the new Kestrel Facilities logo

Target Market(s)

Professional

Industry/Entity Type

Professional services

Contact Information for Business Card

Employee name, title, phone number, email address, corporate office address and logo.

Font styles to use
Sans Serif

Colors
0054AA
0677BA
7BADD7
CADEEF
E8F1F8

Requirements
Must have
• My logo
Should not have
• any other pictures or images besides my logo

```html
<!DOCTYPE html>
<html lang="en">
<head>
<meta charset="utf-8">
<title>Kestrel Facilities – Business Card</title>
<link href="https://fonts.googleapis.com/css2?family=Montserrat:wght@400;500;700&display=swap" rel="stylesheet">
<style>
  :root {
    --brand-blue: #3577be;
    --ink: #1a1a1a;
    --card: #ffffff;
    --backdrop: #e8ebef;
  }
  * { margin: 0; padding: 0; box-sizing: border-box; }
  html, body {
    width: 1160px; height: 1200px; overflow: hidden;
    background: var(--backdrop);
    font-family: "Montserrat", Arial, sans-serif;
  }
  .canvas { position: relative; width: 1160px; height: 1200px; }
  .card {
    position: absolute; left: 199px; width: 778px; height: 441px;
    background: var(--card); overflow: hidden;
  }
  .card--front { top: 105px; }
  .card--back { top: 634px; height: 444px; }

  .brand {
    position: absolute; display: flex; align-items: center; gap: 14px;
    color: var(--brand-blue); font-weight: 700; line-height: 1.05;
  }
  .brand__mark { background: var(--brand-blue); flex: none; }
  .card--front .brand { left: 0; right: 0; top: 74px; justify-content: center; font-size: 44px; }
  .card--front .brand__mark { width: 40px; height: 40px; }
  .card--back .brand { left: 0; right: 0; top: 168px; justify-content: center; font-size: 56px; }
  .card--back .brand__mark { width: 52px; height: 52px; }

  .person {
    position: absolute; right: 406px; top: 240px; text-align: right;
  }
  .person__name {
    color: var(--brand-blue); font-weight: 700; font-size: 29px;
    letter-spacing: -0.3px; line-height: 1.1;
  }
  .person__title { color: var(--ink); font-size: 20px; margin-top: 10px; }

  .divider {
    position: absolute; left: 403px; top: 231px; width: 2px; height: 81px;
    background: var(--brand-blue);
  }
  .contacts { position: absolute; left: 424px; top: 232px; list-style: none; }
  .contacts li {
    display: flex; align-items: center; gap: 8px;
    font-size: 20px; color: var(--ink); height: 29.5px;
  }
  .contacts svg { width: 19px; height: 19px; fill: var(--brand-blue); flex: none; }

  .address {
    position: absolute; left: 0; width: 778px; padding-left: 18px; top: 323px;
    text-align: center; font-size: 20.5px; color: var(--ink);
  }
  .swoosh { position: absolute; left: 0; top: 0; width: 778px; height: 441px; }
  .swoosh path { fill: var(--brand-blue); }
</style>
</head>
<body>
<main class="canvas">
  <section class="card card--front">
    <svg class="swoosh" viewBox="0 0 778 441" aria-hidden="true">
      <path d="M0,388 C300,432 600,392 751,278 C612,382 300,424 0,404 Z"/>
      <path d="M778,272 C620,384 320,446 0,418 L0,441 L778,441 Z"/>
    </svg>

    <div class="brand"><span class="brand__mark"></span><span>Kestrel<br>Facilities</span></div>

    <div class="person">
      <p class="person__name">DANA WHITFIELD</p>
      <p class="person__title">Co-Founder</p>
    </div>

    <span class="divider"></span>

    <ul class="contacts">
      <li>
        <svg viewBox="0 0 24 24" aria-hidden="true"><path d="M6.6 10.8a15.5 15.5 0 0 0 6.6 6.6l2.2-2.2a1 1 0 0 1 1-.25 11.4 11.4 0 0 0 3.6.57 1 1 0 0 1 1 1V20a1 1 0 0 1-1 1A17 17 0 0 1 3 4a1 1 0 0 1 1-1h3.5a1 1 0 0 1 1 1c0 1.25.2 2.45.57 3.57a1 1 0 0 1-.25 1z"/></svg>
        +254-700-55012
      </li>
      <li>
        <svg viewBox="0 0 24 24" aria-hidden="true"><path d="M2 5h20v14H2z M2 5l10 8 10-8" fill="none" stroke="#3577be" stroke-width="2"/></svg>
        info@kestrelfm.com
      </li>
      <li>
        <svg viewBox="0 0 24 24" aria-hidden="true"><circle cx="12" cy="12" r="10"/><path d="M7 8c2 0 3 1 3 3s-2 2-2 4M15 5c0 2 2 3 3 3M14 14c1 0 3 1 3 4" stroke="#fff" stroke-width="1.6" fill="none"/></svg>
        www.kestrelfm.com
      </li>
    </ul>

    <p class="address">4180 N. Harbor Lane Suite 220 Westfield 14</p>
  </section>

  <section class="card card--back">
    <div class="brand"><span class="brand__mark"></span><span>Kestrel<br>Facilities</span></div>
  </section>
</main>
</body>
</html>
```